Systems and Technology Consultants - Website

Design & Build a website for a new company which operates in the Systems and Technology space for Transportation, Government and Commercial sectors.

Overall design should be minimalist in nature.
Should also have a feed that provides news and event updates on the main page.
Logo has already been awarded and should be incorporated into the site.

We like the overall layout, functionality and simplicity of the below sites. Submitted designs could be similar to or a combination of the aspects on these sites, or perhaps a whole different concept - we are open to new ideas.
Norvique.com
Teblo.it

Update 1 Dated 27 May 2014

All I am moving away from the Teblo.it website and would like it to be more aligned with Norvique.com not only in layout but in functionality. I will be extending the deadline of this design brief for two weeks to incorporate additional requirements and will add addtional funding to the project.

Apologies for not having more information available to provide but with so many submissions its getting confusing.

Thanks Derek

Please note that the brief has been updated and the deadline has been extended.

Important: We will need two language versions of the website, English and Arabic; the website is hosted on HostPelican

Hello All, Thank you for your submissions. We have narrowed it down to the final 6 designers and I just wanted to take a moment and provide a bit of feedback regarding the concepts that we like and the modifications we are looking for. First, let me mention some of the design functions we like. - At the top of the homepage we really like the "region" or "language" tab so that the website can be viewed in both English and Arabic. - We like the homepage to have clear color variation so that the different sections of the homepage are distinct. Additionally, we like the bottom portion of the homepage to be in red. We feel that draws attention to our contact information. Again, we would like the colors to integrate black, gray-scale, red, etc. - Having a search tab at the top of the home page, or integrated into the main image, so that the site is easy to navigate. - We especially like the main image to have the scrolling tabs at the bottom so it is easy to browse the services offered (Consultancy, Solutions Architecture, Masters Systems Integration, Independent Design Review). - In regards to the services offered tab we really like the idea that a few people presented that have the outside of our logo with an icon in the middle of consultancy, solutions, etc., etc. Secondly, as mentioned in our brief we really enjoy the design of norvique site. Specially, we enjoy the strong iconic images they use, the way the tabs at the top scroll easily, and contact us page that generates an email. Lastly, I've included some photos of the concept we have been working on. What we are trying to demonstrate is how our company offers a range of services that are essentially linked together. We provide individual services that when combined present the full service package. We would like this concept to be integrated into the over concept of our website. Please feel free to ask for clarification of any of the above points or contact us if you have any additional questions. We appreciate all of your hard work and are very excited to see the updated designs. Best, Marta Vennick Quelbrant Senior Program Manager marta.vennick@quelbrant-example.com

Industry/Entity Type

Government

Font styles to use
Serif
Sans Serif

Requirements
Must have
• Must work on/adapt to various/mobile devices (responsive)
Must be simple and straightforward
Colors should be in line/matching with logo
2 language versions: English and Arabic (no Thai)
Services should be the first group/row of items after/below the main image
Note: the website will be hosted by hostpelican
Nice to have
• Submit feedback form
What's New section
The banner at the bottom of the site should not be too large; we would like a narrow one more
It would be nice if the header/top banner (with Home, About, etc. tabs) could stay in place as you scroll down (like Norvique and Chatterloop)
We will likely only use one image with a Company slogan on the Home page rather than a carousel of images to rotate through
Should not have
• This is the existing website: http://www.quelbrant-example.org
We do not like the animation, the way the banner icons/titles bounce
Not simple enough, we don't like the functionality or how pages load so slowly
We do not like the logo centered - it should be at the left
The banner and its tabs should not be towards the right, we would like them to be centered, to go all the way across and to be below the logo

```html
<!DOCTYPE html>
<html lang="en">
<head>
<meta charset="utf-8">
<title>Quelbrant International – Home</title>
<link href="https://fonts.googleapis.com/css2?family=Open+Sans:wght@300;400;600;700&family=Montserrat:wght@400;600;700&family=Arimo:wght@400;700&display=swap" rel="stylesheet">
<style>
:root{
  --red:#e3202a;
  --footer-red:#d3232a;
  --dark:#2b2b2b;
  --darker:#1d1d1d;
  --ink:#333;
  --muted:#8a8a8a;
  --light:#f1f0f0;
  --hero-a:#0c3346;
  --hero-b:#1a6f8c;
  --hero-c:#33a4c4;
  --white:#fff;
}
*{box-sizing:border-box;margin:0;padding:0}
html,body{width:785px;height:1200px;overflow:hidden;background:var(--white)}
body{position:relative;font-family:"Open Sans",sans-serif;color:var(--ink)}
.abs{position:absolute}

.topbar{left:0;top:0;width:785px;height:16px;background:var(--dark);color:#ddd;font-size:8px;line-height:16px}
.topbar .legal{left:73px}
.topbar .phone{left:534px;display:flex;align-items:center;gap:4px}
.topbar .mail{left:627px;display:flex;align-items:center;gap:5px}

.header{left:0;top:16px;width:785px;height:95px;background:var(--white)}
.brand{left:72px;top:30px;display:flex;align-items:center;gap:10px}
.brand .mark{width:18px;height:18px;background:var(--red)}
.brand .name{font-family:"Montserrat",sans-serif;font-weight:600;font-size:20px;letter-spacing:2px;color:var(--red)}
.lang{left:437px;top:31px;display:flex;align-items:center;gap:6px;font-size:11px;color:#555}
.lang .globe{width:22px;height:12px;border-radius:6px;background:var(--red)}
.search{left:530px;top:27px;width:183px;height:22px;background:#f0f0f0;border:1px solid #e3e3e3;border-radius:2px}
.nav{left:0;top:80px;width:785px;font-size:10px;color:#222}
.nav a{position:absolute;color:inherit;text-decoration:none;white-space:nowrap}
.nav .active{color:var(--red)}
.nav .underline{position:absolute;left:294px;top:16px;width:42px;height:2px;background:var(--red)}

.hero{left:0;top:111px;width:785px;height:288px;background:linear-gradient(90deg,var(--hero-a) 0%,#123e54 45%,var(--hero-b) 75%,var(--hero-c) 100%)}
.hero-photo{left:360px;top:0;width:425px;height:288px;background:radial-gradient(ellipse at 70% 40%,rgba(80,190,220,.55),rgba(15,60,85,0) 70%)}
.hero h1{left:71px;top:76px;font-family:"Montserrat",sans-serif;font-weight:600;font-size:25px;line-height:35px;letter-spacing:1.2px;color:var(--white)}
.hero h1 span{color:var(--red)}
.hero .lead{left:72px;top:153px;width:320px;font-size:15.5px;line-height:18px;color:#e8f1f5;font-weight:300}
.hero .lead b{color:var(--red);font-weight:700}
.hero .cta{left:72px;top:202px;width:123px;height:25px;background:var(--red);border-radius:2px;color:var(--white);font-family:"Montserrat",sans-serif;font-weight:700;font-size:9px;letter-spacing:1.5px;display:flex;align-items:center;justify-content:center;gap:8px}
.hero-shadow{left:20px;top:399px;width:745px;height:14px;background:radial-gradient(ellipse at 50% 0%,rgba(0,0,0,.18),rgba(0,0,0,0) 70%)}

.services-title{left:0;top:424px;width:785px;text-align:center;font-size:22px;font-weight:300;color:#333}
.arrow-btn{top:426px;width:25px;height:25px;border-radius:50%;background:#4a4a4a}
.service{top:472px;width:200px;text-align:center}
.service .icon{margin:0 auto;width:66px;height:66px;border-radius:50%;border:5px solid #c9c9c9}
.service.featured .icon{border-color:var(--red)}
.service h3{margin-top:17px;font-weight:400;font-size:13px;color:#222}
.service p{margin-top:14px;font-size:8.6px;line-height:13px;color:var(--muted)}
.service .more{display:inline-block;margin-top:16px;padding:0 8px;height:19px;line-height:17px;border:1.5px solid #333;font-size:8.5px;color:#222}
.service.featured .more{border-color:var(--red);color:var(--red)}
.divider{top:478px;width:1px;height:200px;background:linear-gradient(#fff,#e6e6e6,#fff)}

.section-title{font-size:14px;font-weight:400;color:#333}
.acc-open{left:84px;top:738px;width:302px;height:144px;background:var(--light)}
.acc-open .side{left:0;top:0;width:26px;height:144px;background:#d8d8d8}
.acc-open .toggle{left:0;top:0;width:26px;height:37px;background:var(--red)}
.acc-open h4{left:36px;top:12px;width:250px;font-weight:400;font-size:10.4px;line-height:13px;color:#222}
.acc-open p{left:36px;top:45px;width:258px;font-size:8px;line-height:13px;color:var(--muted)}
.acc-item{left:84px;width:302px;background:var(--light)}
.acc-item .toggle{left:0;top:0;width:26px;height:100%;background:#3a3a3a}
.acc-item span{position:absolute;left:35px;font-size:9.5px;color:#222}

.news-item{left:427px;width:290px}
.date{left:0;top:0;width:40px;height:39px}
.date .d{height:20px;background:#3a3a3a;color:var(--white);font-size:15px;text-align:center;line-height:21px}
.date .m{height:19px;background:var(--red);color:var(--white);font-size:14px;text-align:center;line-height:18px}
.news-item h5{left:48px;top:-3px;font-weight:400;font-size:11px;color:#222}
.news-item p{left:48px;top:14px;width:226px;font-size:8.2px;line-height:13px;color:var(--muted)}

.footer{left:0;top:1017px;width:785px;height:151px;background:var(--footer-red);color:var(--white);font-family:"Arimo",sans-serif}
.footer .brand{left:72px;top:20px}
.footer .brand .mark{background:var(--white)}
.footer .brand .name{color:var(--white)}
.footer .about{left:76px;top:80px;width:200px;font-size:8.6px;line-height:13px}
.footer h6{font-size:9.6px;font-weight:400;letter-spacing:.3px}
.sitemap{left:280px;top:28px}
.sitemap ul{list-style:none;margin:12px 0 0 6px;font-size:6.8px;font-weight:700;line-height:13.2px}
.events{left:385px;top:28px}
.events ul{list-style:none;margin-top:11px;font-size:8.6px;line-height:17.5px}
.events li{display:flex;align-items:center;gap:7px}
.events li i{display:inline-block;width:6px;height:6px;border:1.5px solid var(--white);transform:rotate(45deg)}
.contact{left:565px;top:24px}
.contact ul{list-style:none;margin-top:12px;font-size:8.6px;font-weight:700}
.contact li{display:flex;align-items:center;gap:10px;height:21px}
.contact li.indent{padding-left:20px}

.bottombar{left:0;top:1168px;width:785px;height:32px;background:var(--darker);color:#cfcfcf;font-size:8.6px;line-height:32px}
.bottombar .copy{left:70px}
.bottombar .follow{left:602px;font-size:10px}
.social{top:9px;width:15px;height:15px;border-radius:50%;background:#4a4a4a}
</style>
</head>
<body>

<div class="abs topbar">
  <span class="abs legal">Terms &nbsp;|&nbsp; Privacy Policy</span>
  <span class="abs phone">
    <svg width="7" height="8" viewBox="0 0 10 10"><path d="M2 0l2 2.5-1.2 1.3c.6 1.3 1.6 2.3 2.9 2.9L7 5.5 9.5 7.5 8.2 9.5C4 9.5.5 6 .5 1.8z" fill="#ddd"/></svg>
    +123 4455 6677</span>
  <span class="abs mail">
    <svg width="10" height="7" viewBox="0 0 10 7"><rect width="10" height="7" fill="#ddd"/><path d="M0 0l5 4 5-4" stroke="#2b2b2b" fill="none"/></svg>
    info@quelbrant-example.com</span>
</div>

<header class="abs header">
  <div class="abs brand"><span class="mark"></span><span class="name">QUELBRANT</span></div>
  <div class="abs lang"><span class="globe"></span>English
    <svg width="8" height="6" viewBox="0 0 8 6"><path d="M0 0h8L4 6z" fill="#e3202a"/></svg></div>
  <div class="abs search">
    <svg class="abs" style="left:164px;top:5px" width="11" height="11" viewBox="0 0 11 11"><circle cx="4.5" cy="4.5" r="3.3" stroke="#222" stroke-width="1.6" fill="none"/><path d="M7 7l3 3" stroke="#222" stroke-width="1.8"/></svg>
  </div>
  <nav class="abs nav">
    <a class="active" style="left:301px">HOME</a>
    <a style="left:363px">Business Units</a>
    <a style="left:458px">Services</a>
    <a style="left:524px">About Us</a>
    <a style="left:595px">Locations</a>
    <a style="left:667px">Contact Us</a>
    <span class="underline"></span>
  </nav>
</header>

<section class="abs hero">
  <div class="abs hero-photo" role="img" aria-label="Photo of a consultant sketching system diagrams and charts on a glowing glass board"></div>
  <h1 class="abs">INTEGRATED <span>SYSTEMS</span><br>RELIABLE SOLUTIONS</h1>
  <p class="abs lead"><b>QUELBRANT</b> Specializes in delivering quality fessional Services and Technical Projects that</p>
  <div class="abs cta">LEARN MORE
    <svg width="18" height="8" viewBox="0 0 18 8"><path d="M1 0l4 4-4 4M8 0l4 4-4 4" stroke="#fff" stroke-width="1.3" fill="none"/></svg></div>
</section>
<div class="abs hero-shadow"></div>

<h2 class="abs services-title">Services offered</h2>
<div class="abs arrow-btn" style="left:651px"><svg width="25" height="25" viewBox="0 0 25 25"><path d="M14 8.5v8l-5-4z" fill="#fff"/></svg></div>
<div class="abs arrow-btn" style="left:687px"><svg width="25" height="25" viewBox="0 0 25 25"><path d="M11 8.5v8l5-4z" fill="#fff"/></svg></div>

<div class="abs service featured" style="left:77px">
  <div class="icon"></div>
  <h3>Consulting</h3>
  <p>Lorem Ipsum is simply dummy text of the printing and typesetting industry. Lorem Ipsum has been the industry's standard dummy text ever since the 1500s.</p>
  <span class="more">Read More</span>
</div>
<div class="abs divider" style="left:287px"></div>
<div class="abs service" style="left:288px">
  <div class="icon"></div>
  <h3>Solutions Architecture</h3>
  <p>Lorem Ipsum is simply dummy text of the printing and typesetting industry. Lorem Ipsum has been the industry's standard dummy text ever since the 1500s.</p>
  <span class="more">Read More</span>
</div>
<div class="abs divider" style="left:498px"></div>
<div class="abs service" style="left:499px">
  <div class="icon"></div>
  <h3>Masters Systems Integration</h3>
  <p>Lorem Ipsum is simply dummy text of the printing and typesetting industry. Lorem Ipsum has been the industry's standard dummy text ever since the 1500s.</p>
  <span class="more">Read More</span>
</div>

<h2 class="abs section-title" style="left:85px;top:708px">Articles</h2>
<div class="abs acc-open">
  <div class="abs side"></div>
  <div class="abs toggle"><svg width="26" height="37" viewBox="0 0 26 37"><path d="M8 13h10" stroke="#fff" stroke-width="1.2"/></svg></div>
  <h4 class="abs">Lorem ipsum dolor sit amet, consectetur adipisicing elit</h4>
  <p class="abs">Lorem Ipsum is simply dummy text of the printing and typesetting industry. Lorem Ipsum has been the industry's standard dummy text ever since the 1500s, when an unknown printer took a galley of type and scrambled it to make a type specimen book. It has survived not only five centuries, but also the leap into electronic typesetting, remaining essentially unchanged. It was popularised in the 1960s.</p>
</div>
<div class="abs acc-item" style="top:890px;height:26px">
  <div class="abs toggle"><svg width="26" height="26" viewBox="0 0 26 26"><path d="M8 13h10M13 8v10" stroke="#fff" stroke-width="1.3"/></svg></div>
  <span style="top:7px">Lorem ipsum dolor sit amet, consectetur adipisicing elit</span>
</div>
<div class="abs acc-item" style="top:922px;height:26px">
  <div class="abs toggle"><svg width="26" height="26" viewBox="0 0 26 26"><path d="M8 13h10M13 8v10" stroke="#fff" stroke-width="1.3"/></svg></div>
  <span style="top:7px">Lorem ipsum dolor sit amet,</span>
</div>
<div class="abs acc-item" style="top:955px;height:37px">
  <div class="abs toggle"><svg width="26" height="37" viewBox="0 0 26 37"><path d="M8 18.5h10M13 13.5v10" stroke="#fff" stroke-width="1.3"/></svg></div>
  <span style="top:12px">Lorem ipsum dolor sit amet, consectetur adipisicing elit</span>
</div>

<h2 class="abs section-title" style="left:427px;top:708px">News</h2>
<div class="abs news-item" style="top:739px">
  <div class="abs date"><div class="d">27</div><div class="m">Feb</div></div>
  <h5 class="abs">Lorem ipsum dolor sit amet,</h5>
  <p class="abs">Lorem Ipsum is simply dummy text of the printing and typesetting industry</p>
</div>
<div class="abs news-item" style="top:807px">
  <div class="abs date"><div class="d">23</div><div class="m">Feb</div></div>
  <h5 class="abs">Lorem ipsum dolor sit amet,</h5>
  <p class="abs">Lorem Ipsum is simply dummy text of the printing and typesetting industry.</p>
</div>
<div class="abs news-item" style="top:875px">
  <div class="abs date"><div class="d">22</div><div class="m">Feb</div></div>
  <h5 class="abs">Lorem ipsum dolor sit amet,</h5>
  <p class="abs">Lorem Ipsum is simply dummy text of the printing and typesetting industry. Lorem Ipsum has been the industry's standard dummy text</p>
</div>
<div class="abs news-item" style="top:946px">
  <div class="abs date"><div class="d">23</div><div class="m">Feb</div></div>
  <h5 class="abs">Lorem ipsum dolor sit amet,</h5>
  <p class="abs">Lorem Ipsum is simply dummy text of the printing and typesetting industry.</p>
</div>

<footer class="abs footer">
  <div class="abs brand"><span class="mark"></span><span class="name">QUELBRANT</span></div>
  <p class="abs about">Lorem ipsum dolorSit amet consecteturAdipsic-ing elit.ed do euismodTempor incidunt Labore et dolorMagna aliqua.Lorem ipsum dolorSit amet consecteturAdipsicing elit,</p>
  <div class="abs sitemap"><h6>SITE MAP</h6>
    <ul><li>HOME</li><li>ABOUT US</li><li>BUSINESS UNITS</li><li>SERVICES</li><li>LOCATIONS</li><li>CONTACT US</li></ul>
  </div>
  <div class="abs events"><h6>UP COMING EVENTS</h6>
    <ul>
      <li><i></i>Monday 07:00 AM — 07:00 PM</li>
      <li><i></i>Tuesday 07:00 AM — 07:00 PM</li>
      <li><i></i>Wednesday 07:00 AM — 07:00 PM</li>
      <li><i></i>Thursday 07:00 AM — 07:00 PM</li>
    </ul>
  </div>
  <div class="abs contact"><h6>OUR CONTACT INFORMATION</h6>
    <ul>
      <li><svg width="9" height="11" viewBox="0 0 9 11"><path d="M4.5 0A4 4 0 0 0 .5 4c0 3 4 7 4 7s4-4 4-7a4 4 0 0 0-4-4z" fill="#fff"/><circle cx="4.5" cy="4" r="1.5" fill="#d3232a"/></svg>Quelbrant International</li>
      <li class="indent">74, Harbor Lane Springfield</li>
      <li><svg width="9" height="11" viewBox="0 0 9 11"><rect x="1" y="0" width="7" height="11" rx="1" fill="#fff"/><rect x="2.2" y="1.5" width="4.6" height="6.5" fill="#d3232a"/></svg>(555) 014 27 90</li>
      <li><svg width="11" height="8" viewBox="0 0 11 8"><rect width="11" height="8" fill="#fff"/><path d="M0 0l5.5 4.5L11 0" stroke="#d3232a" fill="none"/></svg>info@quelbrant-example.com</li>
    </ul>
  </div>
</footer>

<div class="abs bottombar">
  <span class="abs copy">Copyrights © 2014quelbrant-example.com - All Rights Reserved</span>
  <span class="abs follow">Follow Us</span>
  <span class="abs social" style="left:657px"></span>
  <span class="abs social" style="left:677px"></span>
  <span class="abs social" style="left:698px"></span>
</div>

</body>
</html>
```